Online tuition webpage design needed

Hi,
We are starting up an online tuition website for non- English speakers wishing to take an TOVAR test.

The webpage must include a place for people to enroll online in the course.
The home page must have:
• room for a logo (coming shortly, blue in colour)
• different packages of online tuition and paywick
• tool bar showing different pages
• perhaps a video, small pictures

This is my site currently:-

www.lexavotutoring.com

as you can see, I am not very sure how to create a website … The large logo is what I would like to use, but I project has not been finalized yet. Please note, I don’t like the logo being that large!

Sites that are similar to what I am doing and like the design of are:

http://www.brindacourse.com.au/fees

https://www.quorvel9x.net/index.php

http://www.lessonmasterpercival.co.uk/index.html

http://www.tamrunexamhub.com/

One thing I need is a place for student s to enroll, and if possible, I would like to use learnix to create exercises for students.
Currently, my site is using sitecraft. My preference is to use learnix for online activities. I am not sure if I can use both.
Thanks in advance

Target Market(s)

people wising to take an TOVAR test (English proficiency test)

Industry/Entity Type

Online

Colors
3276b5
0292cd

Requirements
Must have
• a place for enrollment and admin login for students
learnix
video
voxly, friendbook, chirpnet logos
Nice to have
• a booking calender
Should not have
• too much clutter. must be clean and professional looking

```html
<!DOCTYPE html>
<html lang="en">
<head>
<meta charset="utf-8">
<title>TOVAR Online Tuition</title>
<link href="https://fonts.googleapis.com/css2?family=Open+Sans:wght@400;600;700&display=swap" rel="stylesheet">
<style>
:root{
  --backdrop:#3276b5;
  --brand:#0292cd;
  --brand-deep:#0b6cc0;
  --nav:#0a8ed4;
  --nav-active:#0672b8;
  --ink:#333;
  --text-blue:#1a8fd0;
  --footer:#2f2f2f;
  --footer-head:#2aa0dc;
  --white:#fff;
}
*{margin:0;padding:0;box-sizing:border-box}
html,body{width:746px;height:1200px;overflow:hidden}
body{background:var(--backdrop);font-family:"Open Sans",Arial,sans-serif;color:var(--ink);position:relative}
.page{position:absolute;left:106px;top:26px;width:534px;height:1150px;background:var(--white);overflow:hidden}
.abs{position:absolute}

/* header */
.brand{left:12px;top:10px;display:flex;align-items:center;gap:8px}
.brand-mark{width:40px;height:40px;border-radius:50%;background:var(--brand-deep)}
.brand-name{font-size:34px;font-weight:600;color:var(--brand-deep);line-height:1}
.brand-sub{left:72px;top:55px;font-size:13px;color:#444}
.login-title{left:298px;top:24px;font-size:7px;font-weight:700;color:var(--brand)}
.remember{left:389px;top:24px;font-size:5.5px;color:var(--brand)}
.field{height:14px;border:1px solid #ccc;font-size:5.5px;color:#aaa;padding:3px 4px}
.btn{height:13px;background:var(--brand);color:#fff;font-size:7px;font-weight:700;display:flex;align-items:center;justify-content:center;width:41px}

/* nav */
.nav{left:0;top:76px;width:534px;height:26px;background:var(--nav)}
.nav span{position:absolute;top:0;height:26px;line-height:26px;font-size:7px;font-weight:600;color:#fff;transform:translateX(-50%)}
.nav .active{background:var(--nav-active);width:48px;text-align:center}

/* hero */
.hero{left:0;top:102px;width:534px;height:236px;background:linear-gradient(120deg,#7a5a44 0%,#c9a88e 35%,#e9dccf 55%,#a7b8c8 80%,#6e7f90 100%)}
.hero-card{left:315px;top:134px;width:168px;height:168px;border-radius:50%;background:rgba(255,255,255,.78);text-align:center;padding-top:32px}
.hero-card .kicker{font-size:7px;font-weight:700;color:#333}
.hero-card .title{font-size:9.5px;font-weight:700;color:var(--brand);margin-bottom:14px}
.hero-card p{font-size:6.4px;line-height:1.45;color:#444;width:142px;margin:0 auto 6px}

/* packages */
.package{top:362px;width:162px;height:278px;background:var(--brand);color:#fff;padding:14px 16px}
.package.featured{background:var(--brand-deep);box-shadow:0 0 4px rgba(0,0,0,.35)}
.package h3{font-size:15px;font-weight:700;letter-spacing:.3px}
.package .icon{position:absolute;right:10px;top:16px}
.package .desc{font-size:7.3px;line-height:1.25;margin-top:24px;height:62px;width:124px}
.package ul{list-style:none;font-size:7.3px;line-height:13.3px}
.package li{padding-left:12px;position:relative}
.package li.tick::before{content:"\2714";position:absolute;left:0;font-size:6.5px}
.package .price{position:absolute;left:0;right:0;top:208px;text-align:center;font-size:29px;font-weight:700}
.package .price small{font-size:17px}
.package .enroll{position:absolute;left:0;right:0;top:252px;text-align:center;font-size:10px;font-weight:700}
.paywick{right:13px;top:642px;font-size:9.5px;font-weight:700;color:#1b3a6b}

/* intro */
.intro h2{font-size:15px;font-weight:700;color:var(--brand)}
.intro p{font-size:6.8px;color:var(--text-blue);line-height:1.4;width:330px;margin-top:6px}
.intro ul{list-style:none;margin-top:10px;margin-left:12px}
.intro li{font-size:6.8px;color:var(--text-blue);line-height:15px;padding-left:8px;position:relative}
.intro li::before{content:"";position:absolute;left:0;top:5px;border-left:3px solid #555;border-bottom:3px solid transparent}

/* calendar */
.calendar{left:370px;top:669px;width:151px;height:123px;border:1px solid var(--brand)}
.calendar .head{background:var(--brand);color:#fff;font-size:6.5px;font-weight:700;height:14px;line-height:14px;padding-left:10px}
.calendar .grid{display:grid;grid-template-columns:repeat(7,19px);grid-auto-rows:10.6px;margin:8px 0 0 12px;font-size:6.8px;color:#333}
.calendar .grid .dow{color:var(--brand);height:17px}
.calendar .pager{display:flex;justify-content:space-between;font-size:6.5px;font-weight:700;color:var(--brand);padding:9px 14px 0 14px}

/* video */
.section-title{font-size:13.5px;font-weight:700;color:var(--brand)}
.video{left:12px;top:846px;width:267px;height:152px;background:linear-gradient(180deg,#2b3a2a 0%,#3f5a35 45%,#24301f 100%)}
.learnix-mark{left:322px;top:850px;width:30px;height:30px;background:#f39a1c}
.learnix-title{left:378px;top:866px;font-size:13px;font-weight:700;color:var(--brand)}
.learnix-text{left:321px;top:897px;width:176px;font-size:6px;line-height:1.75;color:var(--text-blue)}

/* footer */
.footer{left:0;top:1016px;width:534px;height:134px;background:var(--footer);color:#fff}
.footer h4{position:absolute;font-size:9px;font-weight:700;color:var(--footer-head)}
.footer .links{position:absolute;left:12px;top:36px;list-style:none}
.footer .links li{font-size:7.3px;line-height:13.3px;padding-left:8px;position:relative}
.footer .links li::before{content:"";position:absolute;left:0;top:4px;border-left:3px solid #ccc;border-bottom:3px solid transparent}
.social{position:absolute;display:flex;align-items:center;gap:5px;font-size:9.5px;font-weight:700}
.social i{width:15px;height:15px;border-radius:50%;background:#2b8fd6;display:block}
.social i.ring{background:none;border:1.5px solid #2aa0dc}
.footer .post{position:absolute;left:385px;top:34px;width:140px;font-size:6.6px;line-height:1.6}
.footer .bottom{position:absolute;left:12px;top:104px;font-size:6.6px;font-weight:600}
.footer .bottom span{position:absolute;white-space:nowrap}
.footer .copy{position:absolute;left:12px;top:121px;font-size:6px;color:#777}
</style>
</head>
<body>
<div class="page">

  <!-- header -->
  <div class="abs brand"><span class="brand-mark"></span><span class="brand-name">TOVAR</span></div>
  <div class="abs brand-sub">Online Tuition</div>

  <div class="abs login-title">STUDENTS LOGIN</div>
  <div class="abs remember">&#10003; Remember Password?</div>
  <div class="abs field" style="left:298px;top:33px;width:87px">User Name</div>
  <div class="abs field" style="left:389px;top:33px;width:87px">Password</div>
  <div class="abs btn" style="left:481px;top:34px">LOGIN</div>
  <div class="abs field" style="left:298px;top:53px;width:178px"></div>
  <svg class="abs" style="left:465px;top:56px" width="8" height="8" viewBox="0 0 8 8"><circle cx="3.2" cy="3.2" r="2.3" fill="none" stroke="#bbb" stroke-width="1"/><line x1="5" y1="5" x2="7.5" y2="7.5" stroke="#bbb" stroke-width="1"/></svg>
  <div class="abs btn" style="left:481px;top:54px">SEARCH</div>

  <nav class="abs nav">
    <span class="active" style="left:37px">HOME</span>
    <span style="left:114px">TUTORIAL PACKAGES</span>
    <span style="left:215px">TIPS &amp; COMMENTS</span>
    <span style="left:294px">READING</span>
    <span style="left:358px">SPEAKING</span>
    <span style="left:426px">LISTERNING</span>
    <span style="left:492px">WRITING</span>
  </nav>

  <!-- hero -->
  <div class="abs hero" role="img" aria-label="Group of smiling students lying in a circle giving thumbs up"></div>
  <div class="abs hero-card">
    <div class="kicker">WELCOME TO</div>
    <div class="title">TOVAR ONLINE TUITION</div>
    <p>We put you first. We listen to you and help you find what you need.</p>
    <p>If you want help in passing an TOVAR test, we can help you Lessons in reading, writing, listening and speakingtips.</p>
    <svg width="22" height="12" viewBox="0 0 22 12" style="margin-top:5px"><polyline points="7,1 3,6 7,11" fill="none" stroke="#1b6fb8" stroke-width="1.3"/><polyline points="15,1 19,6 15,11" fill="none" stroke="#1b6fb8" stroke-width="1.3"/></svg>
  </div>

  <!-- packages -->
  <section class="abs package" style="left:12px">
    <h3>SILVER</h3>
    <svg class="icon" width="20" height="20" viewBox="0 0 20 20"><line x1="3" y1="17" x2="17" y2="3" stroke="#c24" stroke-width="3"/><line x1="3" y1="17" x2="5" y2="15" stroke="#777" stroke-width="3"/></svg>
    <p class="desc">Last minute TOVAR preparation. Ideal for thosewho need to get familiar with test format and strategies.</p>
    <ul>
      <li class="tick">90 days access</li>
      <li class="tick">100 hours study time</li>
      <li class="tick">Over 1000 Study Pages</li>
      <li class="tick">Over 260 Interactive Activitie</li>
      <li>Voice recording tools</li>
      <li>Practice tests in all 4 modules</li>
    </ul>
    <div class="price"><small>$</small>59</div>
    <div class="enroll">ENROLL NOW</div>
  </section>

  <section class="abs package featured" style="left:186px">
    <h3>GOLD</h3>
    <svg class="icon" width="22" height="22" viewBox="0 0 22 22"><circle cx="9" cy="7" r="4" fill="#9cb3c9"/><rect x="3" y="12" width="12" height="8" rx="3" fill="#7b93ab"/><circle cx="15" cy="9" r="3.5" fill="#c4d2df"/><rect x="10" y="13" width="10" height="7" rx="3" fill="#a3b6c8"/></svg>
    <p class="desc">Comprehensive TOVAR preparation. Ideal for those who want to improve their English skills and get familiar with the test format and strategies.</p>
    <ul>
      <li class="tick">90 days access</li>
      <li class="tick">100 hours study time</li>
      <li class="tick">Over 1000 Study Pages</li>
      <li class="tick">Over 260 Interactive Activitie</li>
      <li class="tick">Voice recording tools</li>
      <li>Practice tests in all 4 modules</li>
    </ul>
    <div class="price"><small>$</small>79</div>
    <div class="enroll">ENROLL NOW</div>
  </section>

  <section class="abs package" style="left:360px">
    <h3>DIAMOND</h3>
    <svg class="icon" width="20" height="20" viewBox="0 0 20 20"><line x1="3" y1="17" x2="17" y2="3" stroke="#c24" stroke-width="3"/><line x1="3" y1="17" x2="5" y2="15" stroke="#777" stroke-width="3"/></svg>
    <p class="desc">Complete TOVAR preparation. Ideal for those who want to improve their English skills, get familiar with the test and receive personalised assessment</p>
    <ul>
      <li class="tick">90 days access</li>
      <li class="tick">100 hours study time</li>
      <li class="tick">Over 1000 Study Pages</li>
      <li class="tick">Over 260 Interactive Activitie</li>
      <li class="tick">Voice recording tools</li>
      <li class="tick">Practice tests in all 4 modules</li>
    </ul>
    <div class="price"><small>$</small>99</div>
    <div class="enroll">ENROLL NOW</div>
  </section>

  <div class="abs paywick">Paywick</div>

  <!-- intro -->
  <section class="abs intro" style="left:12px;top:664px">
    <h2>TOVAR Online Tuition</h2>
    <p>We put you first. We listen to you and help you find what you need. If you want help in passing an TOVAR test, we can help you with the following criteria,</p>
    <ul>
      <li>Lessons in reading, writing, listening and speaking</li>
      <li>Professional teacher feedback and tips.</li>
      <li>Voxly and practice with native speakers.</li>
      <li>Quick Turnaround.</li>
      <li>Friendly and Approachable teachers</li>
    </ul>
  </section>

  <!-- calendar -->
  <aside class="abs calendar">
    <div class="head">JANUARY 2014</div>
    <div class="grid">
      <span class="dow">M</span><span class="dow">T</span><span class="dow">W</span><span class="dow">T</span><span class="dow">F</span><span class="dow">S</span><span class="dow">S</span>
      <span></span><span></span><span>1</span><span>2</span><span>3</span><span>4</span><span>5</span>
      <span>6</span><span>7</span><span>8</span><span>9</span><span>10</span><span>11</span><span>12</span>
      <span>13</span><span>14</span><span>15</span><span>16</span><span>17</span><span>18</span><span>19</span>
      <span>20</span><span>21</span><span>22</span><span>23</span><span>24</span><span>25</span><span>26</span>
      <span>27</span><span>28</span><span>29</span><span>30</span><span>31</span><span></span><span></span>
    </div>
    <div class="pager"><span>&laquo; DEC</span><span>DEC &raquo;</span></div>
  </aside>

  <!-- video -->
  <h2 class="abs section-title" style="left:12px;top:811px">Video Tutorial</h2>
  <div class="abs video" role="img" aria-label="Video still of a misty pine forest"></div>
  <svg class="abs" style="left:12px;top:846px" width="267" height="152" viewBox="0 0 267 152">
    <circle cx="136" cy="69" r="22" fill="rgba(255,255,255,.12)" stroke="#ccc" stroke-width="2"/>
    <polygon points="130,59 130,79 146,69" fill="#ccc"/>
    <rect x="6" y="130" width="255" height="14" rx="2" fill="rgba(0,0,0,.55)"/>
    <polygon points="14,134 14,140 19,137" fill="#ddd"/>
    <rect x="28" y="136" width="170" height="2" fill="#888"/>
    <rect x="28" y="136" width="18" height="2" fill="#ddd"/>
    <circle cx="46" cy="137" r="2.5" fill="#eee"/>
    <text x="203" y="140" font-size="5.5" fill="#ddd" font-family="Open Sans, sans-serif">1:03 / 4:59</text>
    <polygon points="233,135 236,135 239,133 239,141 236,139 233,139" fill="#ddd"/>
    <path d="M247 134h3M247 134v3M257 134h-3M257 134v3M247 141h3M247 141v-3M257 141h-3M257 141v-3" stroke="#ddd" stroke-width="1" fill="none"/>
  </svg>

  <div class="abs learnix-mark"></div>
  <div class="abs learnix-title">Learnix CMS</div>
  <p class="abs learnix-text">Welcome To Harbourline Language Tuition We put our customers first. We listen to you and help you find what you need. If you want help we are to help you improving your skill with learnix, learnix is a open source course management system (CMS)</p>

  <!-- footer -->
  <footer class="abs footer">
    <h4 style="left:12px;top:16px">TOVAR ONLINE TUITION</h4>
    <ul class="links">
      <li>Reading</li><li>Speaking</li><li>Listening</li><li>Writing</li>
    </ul>
    <div class="social" style="left:146px;top:36px"><i></i>Follow Us</div>
    <div class="social" style="left:146px;top:56px"><i></i>Chirp Us</div>
    <div class="social" style="left:146px;top:75px"><i></i>Link with Us</div>
    <div class="social" style="left:256px;top:36px"><i class="ring"></i>Voxly Call Id</div>
    <h4 style="left:384px;top:16px">LATEST POSTS</h4>
    <p class="post">Welcome To Harbourline Language Tuition We put our customers first. We listen to you and help you find what you need. If you want help...</p>
    <div class="bottom">
      <span style="left:0">Home</span>
      <span style="left:46px">Tutorial Packages</span>
      <span style="left:133px">Tips &amp; Comments</span>
      <span style="left:218px">Reading</span>
      <span style="left:272px">Speaking</span>
      <span style="left:329px">Listerning</span>
      <span style="left:396px">Writing</span>
    </div>
    <div class="copy">Copyright @ TOVAR Online Tuition. All Rights Reserved</div>
  </footer>

</div>
</body>
</html>
```